New Business Card Design Project

Need a design that will create an impact / strong impression towards our clients for our business. We are in the lighting business and we do lighting retrofits for large commercial to industrial clientele.

Target Market(s)

Lighting Industry

Industry/Entity Type

Business

Font styles to use
Other font styles liked:
• we would like to use the font on our logo, not sure what it is though..

Requirements
Must have
• Our logo.
Nice to have
• We are open to suggestions that have to do with lighting.

```html
<!DOCTYPE html>
<html lang="en">
<head>
<meta charset="utf-8">
<title>Lumora Retrofit Group – Business Card</title>
<link href="https://fonts.googleapis.com/css2?family=Open+Sans:wght@400;600&display=swap" rel="stylesheet">
<style>
  :root {
    --page-bg: #3a3a3a;
    --card-black: #050505;
    --card-white: #ffffff;
    --green-dark: #1d4424;
    --green-mid: #2f7d3a;
    --green-light: #6cc04a;
    --text-white: #ffffff;
    --text-grey: #555555;
  }
  * { margin: 0; padding: 0; box-sizing: border-box; }
  html, body {
    width: 1200px; height: 864px; overflow: hidden;
    background: var(--page-bg);
    font-family: "Open Sans", sans-serif;
  }
  .stage {
    position: relative; width: 1200px; height: 864px;
    display: flex; align-items: center; justify-content: center; gap: 40px;
  }
  .card {
    position: relative; width: 540px; height: 309px;
    box-shadow: 0 10px 30px rgba(0,0,0,.45);
    overflow: hidden;
  }
  .card-front { background: var(--card-black); }
  .card-back { background: var(--card-white); }

  .brand {
    position: absolute; display: flex; align-items: center; gap: 10px;
    font-weight: 600; letter-spacing: .5px; white-space: nowrap;
  }
  .brand-mark { width: 18px; height: 18px; }
  .card-front .brand {
    left: 50%; top: 50%; transform: translate(-50%, -50%);
    font-size: 26px; color: var(--text-white);
  }
  .card-front .brand-mark { background: var(--green-light); }
  .card-back .brand {
    left: 34px; top: 48px; font-size: 22px; color: var(--green-dark);
  }
  .card-back .brand-mark { background: var(--green-mid); }

  .name-band {
    position: absolute; left: 0; top: 140px; width: 470px; height: 50px;
    background: var(--green-dark);
  }
  .band-accent {
    position: absolute; left: 478px; top: 140px; width: 34px; height: 50px;
    background: var(--green-light);
  }
  .person {
    position: absolute; left: 34px; top: 143px; color: var(--text-white);
  }
  .person-name { font-size: 21px; font-weight: 600; line-height: 1.25; }
  .person-title { font-size: 14px; line-height: 1.2; }

  .contacts {
    position: absolute; left: 34px; top: 206px; list-style: none;
    color: var(--text-grey); font-size: 15px; line-height: 22px;
  }
  .contacts li { display: flex; align-items: center; gap: 8px; }
  .contacts svg { width: 12px; height: 12px; fill: var(--green-mid); flex: none; }

  .address {
    position: absolute; right: 40px; top: 210px; text-align: right;
    color: var(--text-grey); font-size: 15px; line-height: 22px;
    font-style: normal;
  }
</style>
</head>
<body>
<main class="stage">
  <section class="card card-front" aria-label="Card front">
    <div class="brand"><span class="brand-mark"></span>Lumora Retrofit Group, LLC</div>
  </section>

  <section class="card card-back" aria-label="Card back">
    <div class="brand"><span class="brand-mark"></span>Lumora Retrofit Group, LLC</div>
    <div class="name-band"></div>
    <div class="band-accent"></div>
    <div class="person">
      <p class="person-name">Alex Morgan</p>
      <p class="person-title">President</p>
    </div>
    <ul class="contacts">
      <li><svg viewBox="0 0 24 24"><path d="M6.6 10.8a15 15 0 0 0 6.6 6.6l2.2-2.2a1 1 0 0 1 1-.25 11.4 11.4 0 0 0 3.6.6 1 1 0 0 1 1 1V20a1 1 0 0 1-1 1A17 17 0 0 1 3 4a1 1 0 0 1 1-1h3.5a1 1 0 0 1 1 1c0 1.25.2 2.45.6 3.6a1 1 0 0 1-.25 1z"/></svg>01 012-345-6789</li>
      <li><svg viewBox="0 0 24 24"><path d="M7 1h10a2 2 0 0 1 2 2v18a2 2 0 0 1-2 2H7a2 2 0 0 1-2-2V3a2 2 0 0 1 2-2zm0 3v14h10V4z"/></svg>01 012-345-6780</li>
      <li><svg viewBox="0 0 24 24"><path d="M2 5h20v14H2zm2 2v.5l8 5 8-5V7z"/></svg>info@yourwebsite.com</li>
      <li><svg viewBox="0 0 24 24"><path d="M12 2a10 10 0 1 0 0 20 10 10 0 0 0 0-20zm0 2c.9 1.2 1.6 2.6 2 4h-4c.4-1.4 1.1-2.8 2-4zM4.3 14a8 8 0 0 1 0-4h3.4a16 16 0 0 0 0 4zm5.7 0a14 14 0 0 1 0-4h4a14 14 0 0 1 0 4zm6.3 0a16 16 0 0 0 0-4h3.4a8 8 0 0 1 0 4zM10 16h4c-.4 1.4-1.1 2.8-2 4-.9-1.2-1.6-2.6-2-4z"/></svg>yourwebsite.com</li>
    </ul>
    <address class="address">Street Name, Suite 100<br>State, Zip Code, Country</address>
  </section>
</main>
</body>
</html>
```